custom hat sales

🎨 Project Title:
Custom hat Designer Web Page for WooCommerce (French Texts Provided) i show you exemple what i need

📄 Project Description:
We are looking to create a web page design (desktop and mobile) for a custom cap ordering experience. This page will be integrated into our existing WooCommerce transactional site. The goal is to allow customers to configure and order personalized caps easily and visually.

The entire interface will ultimately be in French, but you can design using placeholder texts (we will provide the actual French text later).

💡 Page Goals & Features:
The page should be modern, clean, and conversion-oriented, and include the following features:

Header area:

Visually showcase examples of designed caps (carousel or grid layout)

A clear title and short description

Customization Steps (in order):

Material selection: users choose the type of material for the cap

Cap color: users choose the base color of the cap

Patch shape: users select the shape of the patch (e.g., round, square, rectangle, custom)

Patch location: mainly the front, but possibly add other options

Quantity selection: users choose how many units they want (with price updates)

Price display: show price per unit and total cost depending on quantity

Call to Action (CTA):

Add to cart or request a quote button

Smooth integration with WooCommerce logic (cart, checkout, etc.)

Other Optional Sections:

FAQ

Delivery timeline

Client testimonials or reviews

🛠 Technical Notes:
The design must be compatible with WooCommerce

Responsive design for both desktop and mobile

The final output can be delivered in Figma, Adobe XD, or layered PSD (no coding required for now)

We will handle the French translation; just use placeholder text where needed

🖼 Inspiration / Style:
Clean and modern layout

Easy to navigate

Visual configurator-style approach (like t-shirt or shoe customization sites)

Feel free to use mockups of caps to enhance the presentation

📎 What we will provide:
Actual French text

Product images (caps, patch styles, color swatches)

Brand logo and colors

Optional references if needed

✅ Deliverables:
Homepage (or dedicated product page) layout

Mobile and desktop views

Editable design file (Figma, XD, PSD)

i need very nice 1 or 2 hat design to present to customer design un der the hat and front and see coupple of shape of the patche to show option possible

```html
<!DOCTYPE html>
<html lang="en">
<head>
<meta charset="utf-8">
<title>Custom Hat</title>
<link href="https://fonts.googleapis.com/css2?family=Poppins:ital,wght@0,400;0,500;0,600;0,700;0,800;1,400&display=swap" rel="stylesheet">
<style>
:root{
  --orange:#ef9f1f;
  --green:#5db929;
  --ink:#2b2b2b;
  --text:#444;
  --grey-bg:#efefef;
  --topbar:#f1f1f1;
  --footer:#3a3a3a;
  --footer-line:#555;
  --footer-text:#e6e6e6;
  --white:#fff;
}
*{box-sizing:border-box;margin:0;padding:0}
html,body{width:1200px;height:3365px;overflow:hidden}
body{font-family:'Poppins',sans-serif;color:var(--text);background:var(--white);position:relative}
.abs{position:absolute}
.btn{display:flex;align-items:center;justify-content:center;color:var(--white);font-weight:600;text-transform:uppercase;background:var(--orange);letter-spacing:.5px}
.section-title{font-weight:600;color:var(--ink);text-transform:uppercase;font-size:35px;letter-spacing:.5px}

.topbar{top:0;left:0;width:1200px;height:52px;background:var(--topbar);font-size:14px;font-weight:500;color:#333}
.topbar .contact{left:74px;top:16px;display:flex;gap:20px}
.topbar .contact span::before{content:"";display:inline-block;width:10px;height:10px;background:var(--green);border-radius:2px;margin-right:8px}
.topbar .account{right:73px;top:16px;font-size:13px}

.logo{left:74px;top:76px;font-size:27px;font-weight:500;color:var(--ink);letter-spacing:.5px}
.nav{left:304px;top:83px;display:flex;gap:30px;font-size:13px;font-weight:500;color:#333}
.nav .active{color:var(--orange)}
.header-icons{left:1080px;top:83px;display:flex;gap:20px}
.header-icons i{display:block;width:11px;height:11px;border:2px solid #333;border-radius:50%}
.header-icons i.bag{border-radius:2px;background:#333}

.hero{left:74px;top:125px;width:762px;height:527px;background:linear-gradient(100deg,#fed315 0%,#fbc720 40%,#d8b27a 70%,#c9a26c 100%)}
.hero-text{left:98px;top:320px;width:290px}
.hero-text h1{font-size:42px;font-weight:700;color:var(--ink);line-height:1.1}
.hero-text p{font-size:16px;color:#333;margin-top:14px;line-height:1.5}
.hero-btn{left:100px;top:469px;width:158px;height:50px;font-size:17px}
.arrow{width:32px;height:32px;border-radius:50%;display:flex;align-items:center;justify-content:center}
.arrow.prev{left:88px;top:598px;background:var(--white)}
.arrow.next{left:132px;top:598px;background:#3a3a3a}
.promo-a{left:854px;top:125px;width:273px;height:251px;background:var(--orange);color:var(--white);text-align:center;font-weight:800;text-transform:uppercase}
.promo-a .small{font-size:21px;margin-top:43px}
.promo-a .big{font-size:70px;line-height:1;margin-top:2px}
.promo-a .big span{font-size:34px}
.promo-a .tail{font-size:25px;line-height:1.25;margin-top:12px}
.promo-b{left:854px;top:401px;width:273px;height:251px;background:#3f3f3f}
.promo-b .art{left:20px;top:18px;width:233px;height:140px;background:linear-gradient(135deg,#8a7550,#c7a66b 50%,#e4d33c);border-radius:4px}
.promo-b .label{left:0;top:170px;width:273px;text-align:center;color:var(--white);font-size:21px;font-weight:700;line-height:1.35}

.about-title{left:0;top:709px;width:1200px;text-align:center}
.about-text{left:74px;top:768px;width:1052px;text-align:center;font-size:15px;line-height:27px;color:#444}
.about-btn{left:511px;top:908px;width:179px;height:58px;font-size:19px}

.custom-bg{left:0;top:1049px;width:1200px;height:589px;background:var(--grey-bg)}
.custom-img{left:74px;top:1124px;width:514px;height:438px;background:linear-gradient(160deg,#6f8f5a 0%,#b5a27a 45%,#d3b07c 70%,#5a4a3a 100%)}
.custom-title{left:615px;top:1113px;font-size:33px}
.custom-intro{left:615px;top:1168px;width:512px;font-size:15px;line-height:27px;color:#444}
.select{height:55px;background:var(--white);display:flex;align-items:center;justify-content:space-between;padding:0 16px;font-size:13px;font-weight:500;color:#333}
.select::after{content:"";width:8px;height:11px;background:#222;clip-path:polygon(50% 0,100% 40%,0 40%,0 60%,100% 60%,50% 100%)}
.price{left:898px;top:1448px;font-size:27px;font-weight:600;color:var(--ink)}
.cart-btn{left:615px;top:1507px;width:250px;height:55px;background:var(--green);font-size:16px}
.quote-btn{left:877px;top:1507px;width:250px;height:55px;font-size:16px}

.testi-title{left:0;top:1693px;width:1200px;text-align:center}
.card{top:1764px;width:330px;height:214px;border:1px solid #ddd;background:var(--white);text-align:center;padding:18px 16px}
.card.raised{box-shadow:0 4px 14px rgba(0,0,0,.15);border-color:transparent}
.card p{font-style:italic;font-size:15px;line-height:25.5px;color:#444}
.card .name{font-weight:600;font-size:14px;color:var(--ink);margin-top:14px}
.stars{display:flex;justify-content:center;gap:6px;margin-top:4px}
.stars i{width:13px;height:13px;background:var(--orange);clip-path:polygon(50% 0,61% 35%,98% 35%,68% 57%,79% 91%,50% 70%,21% 91%,32% 57%,2% 35%,39% 35%)}
.chev{width:18px;height:30px}

.delivery{left:0;top:2048px;width:1200px;height:338px;background:linear-gradient(90deg,#fbf1e3,#f3e1c4)}
.delivery-art{left:95px;top:2073px;width:350px;height:285px;background:linear-gradient(135deg,#3c5fc0 0%,#2f4aa0 50%,#e9c590 100%);border-radius:4px}
.delivery-title{left:503px;top:2090px;font-size:33px}
.delivery-text{left:503px;top:2142px;width:610px;font-size:15px;line-height:27px;color:#444}
.delivery-btn{left:503px;top:2276px;width:178px;height:58px;font-size:19px}

.faq-title{left:74px;top:2436px;font-size:33px}
.faq-list{left:74px;top:2495px;width:514px}
.faq-item{display:flex;justify-content:space-between;align-items:center;height:45px;border-bottom:1px solid #ddd;font-size:15px;color:#333}
.faq-item::after{content:"+";width:13px;height:13px;border-radius:50%;background:#333;color:var(--white);font-size:12px;line-height:13px;text-align:center;font-weight:700}
.faq-item.open{border:none;height:auto;padding-top:12px;font-weight:600;color:var(--ink)}
.faq-item.open::after{content:"–"}
.faq-answer{font-size:13px;line-height:24px;color:#444;margin-top:6px}
.faq-btn{left:74px;top:2814px;width:201px;height:59px;font-size:19px}
.faq-img{left:615px;top:2455px;width:512px;height:417px;background:linear-gradient(180deg,#4f86c6 0%,#a8c9e6 35%,#3f8fb0 50%,#9fb58a 65%,#e8e2d4 100%)}

.footer{left:0;top:2958px;width:1200px;height:407px;background:var(--footer);color:var(--footer-text)}
.f-head{font-size:16px;font-weight:600;color:var(--white);text-transform:uppercase}
.f-text{font-size:13px;line-height:27px}
.f-links{font-size:13px;line-height:29.5px}
.newsletter{left:793px;top:3112px;width:324px;height:56px;border:1px solid #ccc;display:flex;align-items:center;justify-content:space-between;padding:0 9px 0 18px;font-size:13px;color:var(--footer-text)}
.newsletter b{width:51px;height:40px;background:var(--green);display:flex;align-items:center;justify-content:center}
.social{left:793px;top:3236px;display:flex;gap:10px;font-size:12px;font-weight:500;color:var(--footer-text)}
.social span{display:flex;align-items:center;gap:5px}
.social span::before{content:"";width:8px;height:8px;border-radius:50%;background:var(--footer-text)}
.footer-line{left:0;top:3298px;width:1200px;height:1px;background:var(--footer-line)}
.copyright{left:74px;top:3323px;font-size:12px;color:var(--footer-text)}
.payments{left:900px;top:3322px;display:flex;gap:10px}
.payments span{font-size:10px;font-weight:600;color:#333;background:#eee;padding:3px 5px;border-radius:2px}
</style>
</head>
<body>

<div class="abs topbar">
  <div class="abs contact"><span>Call Us: +155-555-0142</span><span>hello@capatelier.com</span></div>
  <div class="abs account">Login &nbsp;/&nbsp; Register &nbsp;/&nbsp; Wishlist</div>
</div>

<div class="abs logo">CUSTOM HAT</div>
<nav class="abs nav">
  <span class="active">Home</span><span>About Us</span><span>Customization Steps</span><span>FAQ</span><span>Delivery Timeline</span><span>Testimonials</span><span>Contact Us</span>
</nav>
<div class="abs header-icons"><i></i><i class="bag"></i></div>

<div class="abs hero" role="img" aria-label="Straw hats resting on a colourful striped blanket over a yellow background"></div>
<div class="abs hero-text">
  <h1>Custom Hat</h1>
  <p>Nemo enim ipsam voluptatem quia voluptas sit aspernatur aut odit aut fugitsed.</p>
</div>
<div class="abs btn hero-btn">Get Started</div>
<div class="abs arrow prev"><svg width="12" height="12" viewBox="0 0 12 12"><path d="M8 1L3 6l5 5" stroke="#ef9f1f" stroke-width="2.5" fill="none"/></svg></div>
<div class="abs arrow next"><svg width="12" height="12" viewBox="0 0 12 12"><path d="M4 1l5 5-5 5" stroke="#fff" stroke-width="2.5" fill="none"/></svg></div>

<div class="abs promo-a">
  <div class="small">Get Upto</div>
  <div class="big">15% <span>Off</span></div>
  <div class="tail">Bulk Hat<br>Customization</div>
</div>
<div class="abs promo-b">
  <div class="abs art" role="img" aria-label="Straw hat with a colourful round patch"></div>
  <div class="abs label">CUSTOMIZE YOUR<br>OWN HAT</div>
</div>

<h2 class="abs section-title about-title">About Custom Hat</h2>
<p class="abs about-text">Sed ut perspiciatis unde omnis iste natus error sit voluptatem accusantium doloremque laudantium, totam rem aperiam, eaque ipsa quae ab illo inventore veritatis et quasi architecto beatae vitae dicta sunt explicabo. Nemo enim ipsam voluptatem quia &nbsp;voluptas sit aspernatur aut odit aut fugit, sed quia consequuntur magni dolores eos qui ratione voluptatem sequi nesciunt. &nbsp;Neque porro quisquam est, qui dolorem ipsum quia dolor sit amet, consecteturadipisci velit.</p>
<div class="abs btn about-btn">Read More</div>

<div class="abs custom-bg"></div>
<div class="abs custom-img" role="img" aria-label="Straw hat with a dark shield-shaped logo patch on a mountain terrace"></div>
<h2 class="abs section-title custom-title">Customization Steps</h2>
<p class="abs custom-intro">Sed ut perspiciatis unde omnis iste natus error sit voluptatem accusantium doloremque laudantium.</p>
<div class="abs select" style="left:615px;top:1239px;width:512px">Material selection</div>
<div class="abs select" style="left:615px;top:1305px;width:250px">Cap color</div>
<div class="abs select" style="left:877px;top:1305px;width:250px">Patch shape</div>
<div class="abs select" style="left:615px;top:1371px;width:512px">Patch location</div>
<div class="abs select" style="left:615px;top:1439px;width:250px">Select Quantity</div>
<div class="abs price">$00.00</div>
<div class="abs btn cart-btn">Add to Cart</div>
<div class="abs btn quote-btn">Request a Quote</div>

<h2 class="abs section-title testi-title">Client Testimonials</h2>
<svg class="abs chev" style="left:44px;top:1856px" viewBox="0 0 18 30"><path d="M14 3L3 15l11 12" stroke="#333" stroke-width="2" fill="none"/></svg>
<svg class="abs chev" style="left:1138px;top:1856px" viewBox="0 0 18 30"><path d="M4 3l11 12L4 27" stroke="#333" stroke-width="2" fill="none"/></svg>
<div class="abs card" style="left:74px">
  <p>“ Sed ut perspiciatis unde omnis iste natus error sit voluptatem accusantium doloremque laudantium, totam rem aperiam, eaque ipsa quae occaecat cupidatat non..”</p>
  <div class="name">NAME HEADING</div>
  <div class="stars"><i></i><i></i><i></i><i></i><i></i></div>
</div>
<div class="abs card raised" style="left:436px">
  <p>“ Sed ut perspiciatis unde omnis iste natus error sit voluptatem accusantium doloremque laudantium, totam rem aperiam, eaque ipsa quae occaecat cupidatat non..”</p>
  <div class="name">NAME HEADING</div>
  <div class="stars"><i></i><i></i><i></i><i></i><i></i></div>
</div>
<div class="abs card" style="left:798px">
  <p>“ Sed ut perspiciatis unde omnis iste natus error sit voluptatem accusantium doloremque laudantium, totam rem aperiam, eaque ipsa quae occaecat cupidatat non..”</p>
  <div class="name">NAME HEADING</div>
  <div class="stars"><i></i><i></i><i></i><i></i><i></i></div>
</div>

<div class="abs delivery"></div>
<div class="abs delivery-art" role="img" aria-label="Illustration of a courier handing a parcel to a customer at a blue door beside a potted plant"></div>
<h2 class="abs section-title delivery-title">Delivery Timeline</h2>
<p class="abs delivery-text">Sed ut perspiciatis unde omnis iste natus error sit voluptatem accusantium doloremque laudantium, totam rem aperiam, eaque ipsa quae ab illo inventore veritatis et quasi architecto beatae vitae dicta sunt explicabo. Nemo enim ipsam voluptatem quia .</p>
<div class="abs btn delivery-btn">Read More</div>

<h2 class="abs section-title faq-title">FAQ’s</h2>
<div class="abs faq-list">
  <div class="faq-item">Sed ut perspiciatis unde omnis iste natus error sit?</div>
  <div class="faq-item">Voluptatem accusantium doloremque?</div>
  <div class="faq-item">Laudantium, totam rem aperiam?</div>
  <div class="faq-item">Eaque ipsa quae ab illo inventore veritatis et quasi architecto?</div>
  <div class="faq-item open">Deatae vitae dicta sunt explicabo.?</div>
  <p class="faq-answer">Nemo enim ipsam voluptatem quia &nbsp;voluptas sit aspernatur aut odit fugit, sed quia consequuntur magni dolores eos qui ratione voluptatem sequi nesciunt. &nbsp;Neque porro quisquam es.</p>
</div>
<div class="abs btn faq-btn">View All FAQ’s</div>
<div class="abs faq-img" role="img" aria-label="Woven straw hat with a blue band lying on a sandy beach by the sea"></div>

<footer class="abs footer">
  <div class="abs f-head" style="left:74px;top:64px">About Us</div>
  <p class="abs f-text" style="left:74px;top:92px;width:330px">Excepteur sint occaecat cupidatat non proident, sunt in culpa qui officia deserunt mollit anim id est laborum enim ipsam voluptatem quia voluptas sit aspernatur aut odit aut fugit, sed quia consequuntur.</p>
  <div class="abs f-head" style="left:499px;top:64px">Quick Links</div>
  <div class="abs f-links" style="left:499px;top:91px">Home<br>About Us<br>Customization Steps<br>FAQ<br>Delivery Timeline<br>Testimonials<br>Contact Us</div>
  <div class="abs f-head" style="left:793px;top:64px">Newsletter</div>
  <p class="abs f-text" style="left:793px;top:92px;width:330px">Sed ut perspiciatis unde omnis iste natus error sit voluptatem accusantium.</p>
  <div class="abs f-head" style="left:793px;top:236px">Follow Us</div>
</footer>
<div class="abs newsletter">Email Address<b><svg width="16" height="16" viewBox="0 0 16 16"><path d="M1 8L15 1 11 15 8 9z" fill="#fff"/></svg></b></div>
<div class="abs social"><span>Friendnet</span><span>Chirply</span><span>Snapix</span><span>Reelo</span></div>
<div class="abs footer-line"></div>
<div class="abs copyright">Copyright © 2025 Company Name &nbsp;All Rights Reserved</div>
<div class="abs payments"><span>PayWise</span><span>Vistacard</span><span>Mastex</span><span>Findcard</span></div>

</body>
</html>
```